Postcard Design Project A Healthy reminder

Dr.'s Dhelpit and Sirel dunwat. Internal Medicine/Family practice. This postcard will be for our patients that we have not seen in a while. Also we need another postcard (the one your designing) with a different heading for New patient's. Do you offer a price break for that? The only thing we would need to change is the heading. Please let me know. Thank you so much! Also can you use the map on the last postcard and our logo I made? I cant find it. Please feel free to call me or email me.

```html
<!DOCTYPE html>
<html lang="en">
<head>
<meta charset="utf-8">
<title>Annual Exam Reminder Postcard</title>
<link href="https://fonts.googleapis.com/css2?family=Open+Sans:ital,wght@0,300;0,400;0,600;0,700;0,800;1,800&display=swap" rel="stylesheet">
<style>
:root{
  --bg:#9dd3cf;
  --red:#a80d10;
  --red-bright:#c8141a;
  --ink:#1b1b1b;
  --paper:#ffffff;
  --panel:#f1f1f1;
  --silver:#bdbdbd;
  --dark:#1c1c1c;
  --rule:#555555;
}
*{margin:0;padding:0;box-sizing:border-box}
html,body{width:1200px;height:891px;overflow:hidden}
body{background:var(--bg);font-family:"Open Sans",sans-serif;position:relative}
.card{position:absolute;top:247px;width:560px;height:396px;background:var(--paper);overflow:hidden;box-shadow:0 6px 18px rgba(0,0,0,.18)}
.card--front{left:30px}
.card--back{left:610px}
.card svg.shapes{position:absolute;inset:0}
.layer{position:absolute;inset:0}

/* front */
.brand{position:absolute;left:48px;top:42px;display:flex;align-items:center;gap:8px}
.brand__mark{width:18px;height:18px;border:2px solid var(--red)}
.brand__name{font-size:15px;font-weight:600;color:var(--ink)}
.brand__tag{position:absolute;left:74px;top:72px;font-size:7px;font-weight:700;letter-spacing:.8px;color:var(--ink);text-transform:uppercase}
.headline{position:absolute;left:52px;top:112px;color:var(--ink)}
.headline__lead{font-size:21px;font-weight:300;line-height:1.3}
.headline__lead strong{color:var(--red);font-weight:800}
.headline__annual{font-size:40px;font-weight:800;line-height:1;margin-top:8px;letter-spacing:.5px}
.headline__exam{font-size:58px;font-weight:800;line-height:.95;color:var(--red)}
.contact{position:absolute;left:44px;top:300px;color:#fff}
.contact__row{display:flex;align-items:flex-start;gap:7px;font-size:13px;line-height:1.35}
.contact__phone{font-size:24px;font-weight:800;margin:4px 0 2px;align-items:center}
.contact svg{flex:none;margin-top:2px}

/* back */
.practice{position:absolute;left:14px;top:14px;font-size:17px;font-weight:800;font-style:italic;color:var(--red);line-height:1.05}
.practice span{font-weight:300;font-style:normal;color:var(--ink)}
.call{position:absolute;left:16px;top:199px;color:#fff;font-weight:800;font-style:italic;font-size:15px;line-height:1.1;letter-spacing:.5px}
.visit{position:absolute;left:182px;top:200px;width:64px;color:#fff;font-size:6px;font-weight:700;line-height:1.3}
.visit__title{display:flex;align-items:center;gap:3px;font-size:6.5px;letter-spacing:.4px;margin-bottom:1px}
.visit__dot{width:6px;height:6px;border-radius:50%;background:#fff}
.stamp{position:absolute;right:34px;top:36px;width:80px;height:52px;border:1px solid var(--rule)}
.address-line{position:absolute;left:332px;width:190px;height:1px;background:var(--rule)}
.address-line--1{top:160px}
.address-line--2{top:196px}
.address-line--3{top:232px}
</style>
</head>
<body>

<section class="card card--front" aria-label="Postcard front">
  <svg class="shapes" viewBox="0 0 560 396" width="560" height="396">
    <defs>
      <linearGradient id="hallway" x1="0" y1="0" x2="1" y2="1">
        <stop offset="0" stop-color="#e8d8c4"/>
        <stop offset=".5" stop-color="#d9c6ae"/>
        <stop offset="1" stop-color="#9c8f86"/>
      </linearGradient>
    </defs>
    <rect class="panel" width="560" height="396" fill="var(--panel)"/>
    <path class="contact-band" d="M0,290 C110,250 250,262 360,330 L400,396 L0,396Z" fill="var(--red)"/>
    <path class="edge-silver" d="M316,0 C262,120 288,300 398,396 L420,396 C310,300 286,120 340,0Z" fill="var(--silver)"/>
    <path class="edge-red" d="M326,0 C272,120 298,300 408,396 L430,396 C320,300 296,120 350,0Z" fill="var(--red-bright)"/>
    <path class="photo" role="img" aria-label="Photo: two doctors in white coats reviewing a chart in a clinic hallway" d="M346,0 C292,120 318,300 428,396 L560,396 L560,0Z" fill="url(#hallway)"/>
  </svg>
  <div class="layer">
    <div class="brand"><span class="brand__mark"></span><span class="brand__name">Dhelpit T Dunwat, M.D.</span></div>
    <div class="brand__tag">A Primary Care Office</div>
    <div class="headline">
      <p class="headline__lead">A healthy <strong>reminder,</strong></p>
      <p class="headline__lead">It is time for your</p>
      <p class="headline__annual">ANNUAL</p>
      <p class="headline__exam">EXAM.</p>
    </div>
    <div class="contact">
      <p class="contact__row">
        <svg width="10" height="14" viewBox="0 0 10 14"><path d="M5 1a4 4 0 0 1 4 4c0 3-4 8-4 8S1 8 1 5a4 4 0 0 1 4-4z" fill="none" stroke="#fff" stroke-width="1.3"/><circle cx="5" cy="5" r="1.4" fill="#fff"/></svg>
        <span>4820 N. Lorren Avenue Suite 210<br>Halden, Ca 90415</span>
      </p>
      <p class="contact__row contact__phone">
        <svg width="20" height="20" viewBox="0 0 20 20"><circle cx="10" cy="10" r="9" fill="none" stroke="#fff" stroke-width="1.5"/><path d="M7 5.5l1.6 2.4-1 1.2c.7 1.4 1.8 2.5 3.2 3.2l1.2-1 2.4 1.6-.9 1.7c-3.5-.3-6.9-3.7-7.2-7.2z" fill="#fff"/></svg>
        <span>(555) 284-6130</span>
      </p>
      <p class="contact__row">
        <svg width="11" height="11" viewBox="0 0 12 12"><circle cx="6" cy="6" r="5" fill="none" stroke="#fff" stroke-width="1.1"/><ellipse cx="6" cy="6" rx="2.2" ry="5" fill="none" stroke="#fff" stroke-width="1"/><path d="M1 6h10" stroke="#fff" stroke-width="1"/></svg>
        <span>www.dunwatmd.com</span>
      </p>
    </div>
  </div>
</section>

<section class="card card--back" aria-label="Postcard back">
  <svg class="shapes" viewBox="0 0 560 396" width="560" height="396">
    <defs>
      <clipPath id="leftPanel"><path d="M0,0 L250,0 C300,90 280,280 120,396 L0,396Z"/></clipPath>
      <linearGradient id="building" x1="0" y1="0" x2="1" y2="1">
        <stop offset="0" stop-color="#8a8a7e"/>
        <stop offset=".6" stop-color="#4a5640"/>
        <stop offset="1" stop-color="#2f3a2a"/>
      </linearGradient>
    </defs>
    <path class="edge-silver" d="M250,0 C300,90 280,280 120,396 L140,396 C298,280 318,90 268,0Z" fill="var(--silver)"/>
    <path class="edge-red" d="M262,0 C312,90 292,280 132,396 L156,396 C316,280 336,90 286,0Z" fill="var(--red-bright)"/>
    <g clip-path="url(#leftPanel)">
      <rect width="560" height="396" fill="var(--panel)"/>
      <rect class="map" role="img" aria-label="Street map showing the office location" x="0" y="62" width="300" height="134" fill="#e4e6e8"/>
      <rect class="call-bar" x="0" y="192" width="176" height="50" fill="var(--red)"/>
      <rect class="visit-box" x="176" y="196" width="124" height="50" fill="var(--dark)"/>
      <rect class="photo" role="img" aria-label="Photo: office building entrance with glass doors and trees" x="0" y="242" width="300" height="154" fill="url(#building)"/>
    </g>
  </svg>
  <div class="layer">
    <p class="practice">Dr.'s Dhelpit <span>and</span><br>Sirel Dunwat</p>
    <p class="call">CALL NOW<br>(555) 284-6130</p>
    <div class="visit">
      <p class="visit__title">VISIT US ON <span class="visit__dot"></span></p>
      <p>Located on the SE corner of Lorren and Pike.</p>
    </div>
    <div class="stamp"></div>
    <div class="address-line address-line--1"></div>
    <div class="address-line address-line--2"></div>
    <div class="address-line address-line--3"></div>
  </div>
</section>

</body>
</html>
```